Specialised investor in e-mobility and energy wants business card design

We need a business card design that fits our existing corporate design. <The look and feel must be 'sharp'/'clean', dynamic, communicate momentum, professionalism etc (as one would imagine from a firm in the financial sector). We like the idea of a reverse-side of the card that includes the logo, and the name and contact details on the other. We expect the deliverable to be whatever format might be required to be able to get cards printed directly by a service such as kelmo press. Our website is www.zub.capital

```html
<!DOCTYPE html>
<html lang="en">
<head>
<meta charset="utf-8">
<title>ZUB Capital – Business Card</title>
<link href="https://fonts.googleapis.com/css2?family=Montserrat:wght@700&family=Questrial&display=swap" rel="stylesheet">
<style>
  :root {
    --backdrop: #1f1f1f;
    --card-white: #ffffff;
    --forest: #2f4d22;
    --forest-deep: #344f24;
    --leaf: #7bb043;
    --ink: #333333;
  }
  * { box-sizing: border-box; margin: 0; padding: 0; }
  html, body {
    width: 1200px; height: 1059px; overflow: hidden;
    background: var(--backdrop);
  }
  .canvas { position: relative; width: 1200px; height: 1059px; }
  .card {
    position: absolute; left: 256px; width: 688px; height: 392px;
    border-radius: 20px; overflow: hidden;
  }
  .card--front { top: 89px; background: var(--card-white); }
  .card--back { top: 547px; background: var(--forest-deep); display: flex; align-items: center; justify-content: center; }

  .wordmark {
    font-family: "Questrial", sans-serif; font-weight: 400; white-space: nowrap;
  }
  .card--front .wordmark {
    position: absolute; left: 37px; top: 58px; font-size: 46px; color: var(--forest);
    letter-spacing: 0.5px;
  }
  .card--back .wordmark { font-size: 84px; color: #ffffff; letter-spacing: 1px; }

  .holder { position: absolute; right: 32px; top: 170px; text-align: right; }
  .holder__name {
    font-family: "Montserrat", sans-serif; font-weight: 700; font-size: 25px;
    letter-spacing: 1px; color: var(--forest); line-height: 1.1;
  }
  .holder__name .surname { color: var(--leaf); }
  .holder__role {
    font-family: "Questrial", sans-serif; font-size: 16px; color: var(--ink); margin-top: 3px;
  }

  .address {
    position: absolute; left: 37px; top: 209px;
    font-family: "Questrial", sans-serif; font-size: 16px; line-height: 22px; color: var(--ink);
    letter-spacing: 0.3px;
  }
  .contacts { position: absolute; left: 37px; top: 265px; list-style: none; }
  .contacts li {
    display: flex; align-items: center; gap: 7px; height: 27.5px;
    font-family: "Questrial", sans-serif; font-size: 16px; color: var(--ink); letter-spacing: 0.3px;
  }
  .contacts svg { width: 12px; height: 12px; fill: var(--leaf); flex: none; }
</style>
</head>
<body>
<div class="canvas">
  <section class="card card--front" aria-label="Business card front">
    <div class="wordmark">ZUB Capital</div>

    <div class="holder">
      <div class="holder__name">MARTIN <span class="surname">ORVELL</span></div>
      <div class="holder__role">Director/Founder</div>
    </div>

    <address class="address" style="font-style:normal">
      1234 Street Name<br>
      Country Name AB 5748
    </address>

    <ul class="contacts">
      <li>
        <svg viewBox="0 0 24 24" aria-hidden="true"><path d="M6.6 10.8a15.1 15.1 0 0 0 6.6 6.6l2.2-2.2a1 1 0 0 1 1-.25 11.4 11.4 0 0 0 3.6.57 1 1 0 0 1 1 1V20a1 1 0 0 1-1 1A17 17 0 0 1 3 4a1 1 0 0 1 1-1h3.5a1 1 0 0 1 1 1c0 1.25.2 2.45.57 3.57a1 1 0 0 1-.25 1z"/></svg>
        123-480-2917
      </li>
      <li>
        <svg viewBox="0 0 24 24" aria-hidden="true"><path d="M2 5h20v2l-10 6L2 7z M2 9.3l10 6 10-6V19H2z"/></svg>
        info@zub.capital
      </li>
      <li>
        <svg viewBox="0 0 24 24" aria-hidden="true"><circle cx="12" cy="12" r="10"/></svg>
        &nbsp;www.zub.capital
      </li>
    </ul>
  </section>

  <section class="card card--back" aria-label="Business card back">
    <div class="wordmark">ZUB Capital</div>
  </section>
</div>
</body>
</html>
```